Luxury Wine Label for New Startup Winery

We need a wine label for our new winery startup. We have worked with a local designer but do not feel the resulting label / logo have the elevation required to present our brand as a luxury wine. Our winery is called "Quailbrook Vineyards" and we are focused on extremely high quality hand crafted artisan and estate wines from the Pacific Northwest.
We would like to see designs that utilize a tree line, or other imagery that represents the "Quailbrook" part of our company name. Another interesting feature could be wood grain.
A logo will be required based on your design so please design with this in mind:
This logo should be consistent with the wine bottle label design, and should be representative of our high end exclusive wine while giving a sense of place (Oregon/ Pacific Northwest.)
I will supply an image of the design we received from our local designer, PLEASE NOTE: in general we do like wood grain and tree line concepts but feel the execution was poorly done.
ATTN: Logo design should be suitable for use on: Bottles (Red wine/rose/white wine), Bussiness cards, vehicle signage, business signage, etc
P.S.:
If you have a design that is not outside the box we are still interested in seeing it.
Label is for a burgundy style bottle with a label height of 3.5 - 4" and a width of 3.5-4"
any label <= 4"x4" and >=3.5"x3.5" will be acceptable:
HOWEVER Width should be greater than or equal to height due to the bottle format
Target Market(s)
Wine enthusiasts with adequate discretionary budgets to afford $100 bottles of wine.
Industry/Entity Type
Wine / Winery
Requirements
Must have
- A sense of luxury, a feel of exclusivity, and a theme consistent with our product and brand name
Nice to have
- Tree line, wood grain or other wood themes. Serif fonts
Should not have
- anything cheesy, off topic, hard to read script fonts or anything that makes the label hard to read from a few feet away or too busy

```html
<!DOCTYPE html>
<html lang="en">
<head>
<meta charset="utf-8">
<title>Quailbrook Vineyards — Wine Labels</title>
<link rel="stylesheet" href="https://fonts.googleapis.com/css2?family=Cormorant+Garamond:wght@500;600&display=swap">
<style>
  :root {
    --backdrop: #38383b;
    --paper: #efefed;
    --gold: #a98a55;
    --gold-line: #b89a66;
    --ink: #3b3b3b;
    --rose-red: #b8333f;
    --rose-tree: #e2b3ab;
    --syrah-tree: #4a4d4b;
  }
  * { margin: 0; padding: 0; box-sizing: border-box; }
  html, body {
    width: 1200px;
    height: 900px;
    overflow: hidden;
    background: var(--backdrop);
  }
  .canvas {
    position: relative;
    width: 1200px;
    height: 900px;
    display: flex;
    justify-content: center;
    align-items: center;
    gap: 60px;
  }
  .label {
    position: relative;
    width: 480px;
    height: 460px;
    background: var(--paper);
    font-family: "Cormorant Garamond", Georgia, serif;
    color: var(--ink);
    overflow: hidden;
  }
  .label__frame {
    position: absolute;
    inset: 12px;
    border: 1.5px solid var(--gold-line);
    pointer-events: none;
    z-index: 3;
  }
  .label__brand {
    position: absolute;
    top: 62px;
    left: 0;
    right: 0;
    text-align: center;
    color: var(--gold);
    font-weight: 600;
    z-index: 2;
  }
  .label__brand-name {
    display: block;
    font-size: 32px;
    letter-spacing: 0.16em;
    line-height: 1;
  }
  .label__brand-sub {
    display: block;
    margin-top: 6px;
    font-size: 13px;
    letter-spacing: 0.6em;
    padding-left: 0.6em;
  }
  .label__trees {
    position: absolute;
    z-index: 1;
  }
  .label--syrah .label__trees {
    left: 0;
    right: 0;
    top: 150px;
    height: 175px;
    background: linear-gradient(170deg, rgba(74,77,75,0) 0%, rgba(74,77,75,0.55) 35%, var(--syrah-tree) 60%, rgba(74,77,75,0.6) 85%, rgba(74,77,75,0) 100%);
  }
  .label--rose .label__trees {
    left: 0;
    right: 0;
    top: 170px;
    bottom: 30px;
    background: linear-gradient(175deg, rgba(226,179,171,0) 0%, rgba(226,179,171,0.7) 35%, var(--rose-tree) 65%, rgba(226,179,171,0.5) 100%);
  }
  .label__varietal {
    position: absolute;
    left: 0;
    right: 0;
    text-align: center;
    font-weight: 500;
    letter-spacing: 0.14em;
    padding-left: 0.14em;
    z-index: 2;
  }
  .label--syrah .label__varietal {
    top: 335px;
    font-size: 40px;
    color: var(--gold);
  }
  .label--rose .label__varietal {
    top: 160px;
    font-size: 52px;
    color: var(--rose-red);
  }
  .label__origin {
    position: absolute;
    left: 0;
    right: 0;
    top: 388px;
    text-align: center;
    font-size: 15px;
    font-weight: 600;
    letter-spacing: 0.28em;
    padding-left: 0.28em;
    color: var(--ink);
    z-index: 2;
  }
  .label__vintage {
    display: block;
    margin-top: 4px;
    font-size: 17px;
    letter-spacing: 0.22em;
  }
</style>
</head>
<body>
  <main class="canvas">
    <section class="label label--syrah">
      <div class="label__frame"></div>
      <div class="label__brand">
        <span class="label__brand-name">QUAILBROOK</span>
        <span class="label__brand-sub">VINEYARDS</span>
      </div>
      <div class="label__trees" role="img" aria-label="Charcoal silhouette of an evergreen tree line rising across a hillside"></div>
      <h2 class="label__varietal">SYRAH</h2>
      <p class="label__origin">WILLAMETTE VALLEY<span class="label__vintage">— 2024 —</span></p>
    </section>

    <section class="label label--rose">
      <div class="label__frame"></div>
      <div class="label__brand">
        <span class="label__brand-name">QUAILBROOK</span>
        <span class="label__brand-sub">VINEYARDS</span>
      </div>
      <div class="label__trees" role="img" aria-label="Soft blush-pink silhouette of an evergreen forest tree line"></div>
      <h2 class="label__varietal">ROSÉ</h2>
      <p class="label__origin">WILLAMETTE VALLEY<span class="label__vintage">— 2024 —</span></p>
    </section>
  </main>
</body>
</html>
```